Harborline Renewal Business Card Design

Professional and clean design. The design colors should flow with the logo. Two-sided card with the website on the back which is:

www.HarborlineRenewal.example.

"Specializing in Water Damage Restoration"

On the front I need the name, email, phone, and logo.

Name: Darnell Quisby
Email: Darnell@HarborlineRenewal.example
Phone: 555-318-2046 for now

I only have the Preview and Thumbnail right now but should have the source files uploaded within a day or two.

Target Market(s)

Flood victims, home owners with water damage from busted pipes etc...

Industry/Entity Type

Business

Contact Information for Business Card

Name: Darnell Quisby

Font styles to use
Serif
Sans Serif

Requirements
Must have
• Business Card Details Info

```html
<!DOCTYPE html>
<html lang="en">
<head>
<meta charset="utf-8">
<title>Harborline Renewal Business Card</title>
<link rel="stylesheet" href="https://fonts.googleapis.com/css2?family=Cinzel:wght@400;600&family=Open+Sans:wght@400;700&display=swap">
<style>
  :root {
    --canvas-bg: #eceff1;
    --white: #ffffff;
    --text-blue: #1f9fd2;
  }
  * { margin: 0; padding: 0; box-sizing: border-box; }
  html, body {
    width: 1200px; height: 780px; overflow: hidden;
    background: var(--canvas-bg);
  }
  .canvas {
    position: relative; width: 1200px; height: 780px;
    display: flex; align-items: center; justify-content: center; gap: 40px;
  }
  .card {
    position: relative; width: 540px; height: 308px;
    border-radius: 4px; overflow: hidden;
    box-shadow: 0 10px 28px rgba(0,0,0,0.18);
  }
  .card-bg { position: absolute; inset: 0; width: 100%; height: 100%; }

  /* Brand lockup */
  .brand {
    position: absolute; display: flex; align-items: center; gap: 12px;
  }
  .brand-dot {
    width: 38px; height: 38px; border-radius: 50%; background: var(--white);
    flex: none;
  }
  .brand-name {
    font-family: "Cinzel", serif; font-weight: 600; color: var(--white);
    font-size: 16px; letter-spacing: 1.5px; text-transform: uppercase;
    line-height: 1.2; white-space: nowrap;
  }

  /* Front */
  .card-front .brand { left: 28px; top: 196px; }
  .contact {
    position: absolute; right: 22px; top: 40px; text-align: right;
    font-family: "Open Sans", sans-serif; color: var(--text-blue);
  }
  .contact-name {
    font-weight: 700; font-size: 22px; margin-bottom: 12px;
  }
  .contact-line {
    display: flex; justify-content: flex-end; align-items: center; gap: 8px;
    font-size: 12px; line-height: 1; margin-bottom: 8px; white-space: nowrap;
  }
  .contact-icon {
    width: 17px; height: 17px; border-radius: 2px; background: var(--text-blue);
    display: inline-flex; align-items: center; justify-content: center; flex: none;
  }
  .contact-icon svg { width: 11px; height: 11px; }

  /* Back */
  .card-back .brand { left: 50%; top: 78px; transform: translateX(-50%); gap: 14px; }
  .card-back .brand-dot { width: 46px; height: 46px; }
  .card-back .brand-name { font-size: 24px; letter-spacing: 3px; }
  .tagline {
    position: absolute; left: 0; right: 0; top: 158px; text-align: center;
    font-family: "Open Sans", sans-serif; color: var(--white); font-size: 14px;
  }
  .back-web {
    position: absolute; left: 0; right: 0; bottom: 44px;
    display: flex; align-items: center; justify-content: center; gap: 16px;
    font-family: "Open Sans", sans-serif; color: var(--white); font-size: 13px;
  }
  .rule { width: 70px; height: 1px; background: rgba(255,255,255,0.85); }
</style>
</head>
<body>
<main class="canvas">

  <section class="card card-front" aria-label="Card front">
    <svg class="card-bg" viewBox="0 0 540 308" preserveAspectRatio="none" aria-hidden="true">
      <defs>
        <linearGradient id="frontBlue" x1="0" y1="0" x2="1" y2="1">
          <stop offset="0" stop-color="#2a9fd0"/>
          <stop offset="0.6" stop-color="#33b6de"/>
          <stop offset="1" stop-color="#1e8fc2"/>
        </linearGradient>
        <linearGradient id="frontPaper" x1="0" y1="0" x2="1" y2="1">
          <stop offset="0" stop-color="#ffffff"/>
          <stop offset="1" stop-color="#eef1f3"/>
        </linearGradient>
      </defs>
      <rect width="540" height="308" fill="url(#frontBlue)"/>
      <path d="M274 0 Q216 160 242 308 L540 308 L540 0 Z" fill="#8fd6ee"/>
      <path d="M290 0 Q232 160 258 308 L540 308 L540 0 Z" fill="url(#frontPaper)"/>
    </svg>

    <div class="brand">
      <span class="brand-dot"></span>
      <span class="brand-name">Harborline<br>Renewal</span>
    </div>

    <div class="contact">
      <p class="contact-name">Darnell Quisby</p>
      <p class="contact-line">555-318-2046
        <span class="contact-icon"><svg viewBox="0 0 12 12"><path d="M3 1 L5 3 L4 4.5 Q5 7 7.5 8 L9 7 L11 9 L9.5 11 Q4 10.5 1 3 Z" fill="#fff"/></svg></span>
      </p>
      <p class="contact-line">Darnell@HarborlineRenewal.example
        <span class="contact-icon"><svg viewBox="0 0 12 12"><rect x="1" y="3" width="10" height="7" fill="none" stroke="#fff" stroke-width="1.2"/><path d="M1 3 L6 7 L11 3" fill="none" stroke="#fff" stroke-width="1.2"/></svg></span>
      </p>
      <p class="contact-line">www.HarborlineRenewal.example
        <span class="contact-icon"><svg viewBox="0 0 12 12"><circle cx="6" cy="6" r="4.6" fill="none" stroke="#fff" stroke-width="1.1"/><ellipse cx="6" cy="6" rx="2" ry="4.6" fill="none" stroke="#fff" stroke-width="1"/><path d="M1.4 6 H10.6" stroke="#fff" stroke-width="1"/></svg></span>
      </p>
    </div>
  </section>

  <section class="card card-back" aria-label="Card back">
    <svg class="card-bg" viewBox="0 0 540 308" preserveAspectRatio="none" aria-hidden="true">
      <defs>
        <radialGradient id="backBlue" cx="0.55" cy="0.35" r="0.85">
          <stop offset="0" stop-color="#36bde2"/>
          <stop offset="1" stop-color="#1a82b6"/>
        </radialGradient>
      </defs>
      <rect width="540" height="308" fill="url(#backBlue)"/>
    </svg>

    <div class="brand">
      <span class="brand-dot"></span>
      <span class="brand-name">Harborline<br>Renewal</span>
    </div>
    <p class="tagline">Specializing in Water Damage Restoration</p>
    <p class="back-web"><span class="rule"></span>www.HarborlineRenewal.example<span class="rule"></span></p>
  </section>

</main>
</body>
</html>
```